Help me make landing pages for my web application that are mobile friendly

I need to make 2 mobile friendly landing pages for an application. The 2 pages will be related. First I need a home page and then I need a working page. I do not want to change the color scheme or logos. Just layout and design.

```html
<!DOCTYPE html>
<html lang="en">
<head>
<meta charset="utf-8">
<title>ShiftCover – My Assignment</title>
<link href="https://fonts.googleapis.com/css2?family=Lexend:wght@400;500;600&family=Arimo:wght@400;700&display=swap" rel="stylesheet">
<style>
  :root{
    --canvas:#ffffff;
    --purple:#5b3f97;
    --teal:#29b3d6;
    --ink:#1c1c1c;
    --panel:#ece9f2;
    --muted:#9a9a9a;
    --rule:#8a8a8a;
    --track:#d9d5df;
    --complete:#4a7fb0;
    --active:#0b8a1e;
    --white:#ffffff;
  }
  *{box-sizing:border-box;margin:0;padding:0}
  html,body{width:778px;height:1200px;overflow:hidden;background:var(--canvas)}
  body{position:relative;font-family:"Arimo",Arial,sans-serif;color:var(--ink)}
  .screen{position:absolute;left:178px;top:156px;width:422px;height:888px;background:var(--white);border-radius:44px;overflow:hidden;box-shadow:0 0 0 1px #e4e4e4}
  .status-bar{position:absolute;left:38px;top:20px;right:38px;height:18px;font:500 15px "Lexend",sans-serif}
  .status-icons{position:absolute;right:0;top:2px;display:flex;gap:10px;align-items:center}
  .brand{position:absolute;left:40px;top:66px;display:flex;align-items:center;gap:10px}
  .brand-dot{width:26px;height:26px;border-radius:50%;background:var(--teal)}
  .brand-name{font:500 31px "Lexend",sans-serif;color:var(--purple);letter-spacing:-.3px}
  .header-btn{position:absolute;top:70px;width:31px;height:31px;border-radius:6px;display:flex;align-items:center;justify-content:center}
  .header-btn.profile{left:317px;background:var(--purple)}
  .header-btn.menu{left:353px;background:var(--ink)}
  .panel{position:absolute;left:0;top:140px;width:422px;height:760px;background:var(--panel);border:1px solid var(--purple);border-bottom:0;border-radius:48px 48px 0 0}
  .tabs{position:absolute;left:38px;top:42px;width:347px;height:36px;border-bottom:1px solid var(--track)}
  .tab{position:absolute;top:0;font:500 17px "Lexend",sans-serif;color:var(--ink)}
  .tab.current{left:10px;color:var(--purple);font-weight:600}
  .tab.current::after{content:"";position:absolute;left:-10px;top:33px;width:156px;height:3px;background:var(--purple)}
  .tab.other{left:176px}
  .scrollbar{position:absolute;left:408px;top:121px;width:4px;height:540px;background:var(--track);border-radius:2px}
  .scrollbar-thumb{width:4px;height:124px;background:var(--purple);border-radius:2px}
  .assignment{position:absolute;left:38px;width:347px;height:233px;border-bottom:2px solid var(--rule)}
  .avatar{position:absolute;left:12px;top:0;width:63px;height:63px;border-radius:12px;display:flex;align-items:center;justify-content:center}
  .avatar.dark{background:var(--ink)}
  .avatar.teal{background:var(--teal)}
  .avatar.purple{background:var(--purple)}
  .edit{position:absolute;left:330px;top:11px}
  .heading{position:absolute;left:95px;top:10px;font:500 17px "Lexend",sans-serif}
  .row{position:absolute;left:95px;font-weight:700;font-size:13.5px}
  .value{position:absolute;left:227px;font-size:11px;color:var(--muted)}
  .value.strong{font-weight:700}
  .badge{position:absolute;left:205px;height:26px;border-radius:13px;color:var(--white);font-weight:700;font-size:11px;display:flex;align-items:center;justify-content:center}
  .badge.complete{width:95px;background:var(--complete)}
  .badge.active{width:78px;background:var(--active)}
  .nav{position:absolute;left:4px;top:797px;width:414px;height:88px;background:var(--ink);border-radius:44px;display:flex;justify-content:space-around;padding:0 20px}
  .nav-item{display:flex;flex-direction:column;align-items:center;gap:6px;padding-top:28px;color:var(--white);font-weight:700;font-size:12.5px}
</style>
</head>
<body>
<main class="screen">
  <div class="status-bar">10:56
    <div class="status-icons">
      <svg width="12" height="11" viewBox="0 0 12 11"><rect x="0" y="8" width="2" height="3" fill="#1c1c1c"/><rect x="3" y="6" width="2" height="5" fill="#1c1c1c"/><rect x="6" y="3" width="2" height="8" fill="#1c1c1c"/><rect x="9" y="0" width="2" height="11" fill="#bbb"/></svg>
      <svg width="16" height="12" viewBox="0 0 16 12" fill="none" stroke="#1c1c1c" stroke-width="1.8"><path d="M1 4.5a10 10 0 0 1 14 0M3.5 7a6.5 6.5 0 0 1 9 0M6 9.5a3 3 0 0 1 4 0"/></svg>
      <svg width="22" height="11" viewBox="0 0 22 11"><rect x=".5" y=".5" width="19" height="10" rx="1.5" fill="none" stroke="#1c1c1c"/><rect x="2" y="2" width="16" height="7" fill="#1c1c1c"/><rect x="20" y="3.5" width="2" height="4" fill="#1c1c1c"/></svg>
    </div>
  </div>

  <div class="brand"><span class="brand-dot"></span><span class="brand-name">ShiftCover</span></div>
  <div class="header-btn profile"><svg width="13" height="13" viewBox="0 0 20 20" fill="#fff"><circle cx="10" cy="6" r="4.5"/><path d="M2 19a8 6 0 0 1 16 0z"/></svg></div>
  <div class="header-btn menu"><svg width="14" height="12" viewBox="0 0 14 12" stroke="#fff" stroke-width="1.4"><path d="M1 1h12M5 6h8M3 11h10"/></svg></div>

  <section class="panel">
    <nav class="tabs">
      <span class="tab current">My Assignment</span>
      <span class="tab other">Available Openings</span>
    </nav>
    <div class="scrollbar"><div class="scrollbar-thumb"></div></div>

    <article class="assignment" style="top:121px">
      <div class="avatar dark"><svg width="26" height="28" viewBox="0 0 20 20" fill="#fff"><circle cx="10" cy="6" r="4.5"/><path d="M2 19a8 6.5 0 0 1 16 0z"/></svg></div>
      <svg class="edit" width="17" height="17" viewBox="0 0 17 17" fill="none" stroke="#5b3f97" stroke-width="1.3"><path d="M8 2H2v13h13V9"/><path d="M13 1.5l2.5 2.5L8 11.5H5.5V9z"/></svg>
      <h2 class="heading">Subbing For:</h2>
      <span class="row" style="top:44px">Dana Whitfield</span><span class="value" style="top:46px">Teacher</span>
      <span class="row" style="top:73px">Location:</span><span class="value" style="top:75px">RHES</span>
      <span class="row" style="top:104px">Status:</span><span class="badge complete" style="top:98px">Complete</span>
      <span class="row" style="top:139px">Time Slots:</span><span class="value strong" style="top:141px">09/02-09/02 (1h 0m)</span>
    </article>

    <article class="assignment" style="top:354px">
      <div class="avatar teal"><svg width="26" height="28" viewBox="0 0 20 20" fill="#fff"><circle cx="10" cy="6" r="4.5"/><path d="M2 19a8 6.5 0 0 1 16 0z"/></svg></div>
      <svg class="edit" width="17" height="17" viewBox="0 0 17 17" fill="none" stroke="#5b3f97" stroke-width="1.3"><path d="M8 2H2v13h13V9"/><path d="M13 1.5l2.5 2.5L8 11.5H5.5V9z"/></svg>
      <h2 class="heading">Subbing For:</h2>
      <span class="row" style="top:44px">Owen Barlow</span><span class="value" style="top:46px">Administrator</span>
      <span class="row" style="top:73px">Location:</span><span class="value" style="top:75px">RHES</span>
      <span class="row" style="top:104px">Status:</span><span class="badge active" style="top:98px">Active</span>
      <span class="row" style="top:139px">Time Slots:</span><span class="value strong" style="top:141px">07/26 - 08/07 (14h 15m)</span>
    </article>

    <article class="assignment" style="top:588px">
      <div class="avatar purple"><svg width="26" height="28" viewBox="0 0 20 20" fill="#fff"><circle cx="10" cy="6" r="4.5"/><path d="M2 19a8 6.5 0 0 1 16 0z"/></svg></div>
      <svg class="edit" width="17" height="17" viewBox="0 0 17 17" fill="none" stroke="#5b3f97" stroke-width="1.3"><path d="M8 2H2v13h13V9"/><path d="M13 1.5l2.5 2.5L8 11.5H5.5V9z"/></svg>
      <h2 class="heading">Subbing For:</h2>
      <span class="row" style="top:44px">Extra Duty</span><span class="value" style="top:46px">Teacher</span>
    </article>
  </section>

  <nav class="nav">
    <div class="nav-item"><svg width="20" height="20" viewBox="0 0 20 20"><circle cx="10" cy="10" r="10" fill="#fff"/><path d="M5 10l5-4.5 5 4.5v5H5z" fill="#1c1c1c"/></svg>Home</div>
    <div class="nav-item"><svg width="20" height="20" viewBox="0 0 20 20"><circle cx="10" cy="10" r="10" fill="#fff"/><circle cx="10" cy="7.5" r="3" fill="#1c1c1c"/><path d="M4.5 16a5.5 4 0 0 1 11 0z" fill="#1c1c1c"/></svg>Profile</div>
    <div class="nav-item"><svg width="22" height="20" viewBox="0 0 22 20"><path d="M3 11a8 8 0 0 1 16 0" fill="none" stroke="#fff" stroke-width="2"/><rect x="1" y="10" width="4" height="6" rx="1.5" fill="#fff"/><rect x="17" y="10" width="4" height="6" rx="1.5" fill="#fff"/><circle cx="11" cy="12" r="5" fill="#fff"/><circle cx="9" cy="12" r=".9" fill="#1c1c1c"/><circle cx="11" cy="12" r=".9" fill="#1c1c1c"/><circle cx="13" cy="12" r=".9" fill="#1c1c1c"/></svg>Support</div>
    <div class="nav-item"><svg width="20" height="20" viewBox="0 0 20 20" fill="none" stroke="#fff" stroke-width="2"><path d="M3.5 6A8 8 0 1 1 2 10"/><path d="M1.5 3v4h4"/><path d="M10 6v4.5l3 2"/></svg>History</div>
    <div class="nav-item"><svg width="20" height="20" viewBox="0 0 20 20" fill="#fff"><rect x="1" y="1" width="8" height="8" rx="1.5"/><rect x="11" y="1" width="8" height="8" rx="1.5"/><rect x="1" y="11" width="8" height="8" rx="1.5"/><path d="M15 10.5l4.5 4.5-4.5 4.5-4.5-4.5z"/></svg>More</div>
  </nav>
</main>
</body>
</html>
```